Business Cards Needed for Innovative Healthcare Marketing Company

We are a marketing company focused on healthcare. Our company is all about rebranding yourself renewing your image and generating results. The phoenix stands for "reborn" or "rising" which we provide new brands for our clients we take their old brands and renew it with creativity and innovation. I am looking for a business card with color dimension. I have attached an example of a card I think has the look and feel of what I am trying to accomplish. I like that the card example has black and grey font colors, I like the font placement and the small logo, I really like the use of the colors on the right those are the colors of my logo. My logo is phoenix so maybe incorporating flames similar to that design. I would like the back a solid color maybe red with an opaque version of the logo and website. As a marketing company I am always open to creative liberty!

Target Market(s)

Doctors and business professionals.

Industry/Entity Type

Marketing

Contact Information for Business Card

Valcorne Health Care Marketing
Marla Tenwick- CEO
#(512)638-2974
email-marla@valcorne.com
website- valcorne.com

Font styles to use
Sans Serif

Colors
ec1f27
f37122
ffc214
fbed22
fbf289
f04a50

Requirements
Must have
• The logo and required information
Nice to have
• icons by the information
Should not have
• child like font

```html
<!DOCTYPE html>
<html lang="en">
<head>
<meta charset="utf-8">
<title>Valcorne Health Care Marketing — Business Cards</title>
<link href="https://fonts.googleapis.com/css2?family=Open+Sans:wght@300;400;600;700&display=swap" rel="stylesheet">
<style>
  :root {
    --stage: #1a1a1a;
    --card: #ffffff;
    --brand-red: #9b1c22;
    --brand-orange: #e0561a;
    --icon: #e0461f;
    --ink: #3a3a3a;
    --ink-soft: #4a4a4a;
  }
  * { margin: 0; padding: 0; box-sizing: border-box; }
  html, body {
    width: 1200px; height: 900px; overflow: hidden;
    background: var(--stage);
    font-family: "Open Sans", sans-serif;
  }
  .stage { position: relative; width: 1200px; height: 900px; }
  .card {
    position: absolute; top: 306px;
    width: 440px; height: 271px;
    background: var(--card);
    border-radius: 12px;
  }
  .card--front { left: 148px; }
  .card--back { left: 608px; }

  .front-mark {
    position: absolute; left: 78px; top: 70px;
    width: 120px; height: 140px;
    display: flex; flex-direction: column; align-items: center; justify-content: center; gap: 10px;
  }
  .mark-dot {
    width: 46px; height: 46px; border-radius: 50%;
    background: var(--brand-orange);
  }
  .front-mark .mark-name {
    font-size: 17px; font-weight: 400; color: var(--brand-red); letter-spacing: 0.5px;
  }

  .holder { position: absolute; left: 247px; top: 77px; }
  .holder-name { font-size: 15px; font-weight: 700; color: var(--brand-orange); line-height: 18px; }
  .holder-role { font-size: 12px; color: var(--ink-soft); line-height: 16px; }

  .contacts { position: absolute; left: 248px; top: 145px; list-style: none; }
  .contacts li {
    display: flex; align-items: center; gap: 6px;
    font-size: 12.5px; color: var(--ink); line-height: 16px;
  }
  .contacts svg { width: 10px; height: 10px; fill: var(--icon); flex: none; }

  .back-logo {
    position: absolute; left: 0; right: 0; top: 0; bottom: 0;
    display: flex; align-items: center; justify-content: center; gap: 16px;
  }
  .back-logo .mark-dot { width: 64px; height: 64px; }
  .back-logo .mark-name {
    font-size: 24px; font-weight: 300; color: var(--brand-red);
    line-height: 30px; letter-spacing: 1px;
  }
</style>
</head>
<body>
<main class="stage">
  <section class="card card--front" aria-label="Card front">
    <div class="front-mark">
      <span class="mark-dot"></span>
      <span class="mark-name">Valcorne</span>
    </div>
    <div class="holder">
      <p class="holder-name">Marla Tenwick</p>
      <p class="holder-role">CEO</p>
    </div>
    <ul class="contacts">
      <li>
        <svg viewBox="0 0 10 10" aria-hidden="true"><path d="M2.2 0.5l1.6 2-1 1.1c.6 1.3 1.5 2.2 2.6 2.8l1.1-1 2 1.6-.9 1.8C4.6 8.6 1.3 5.3.4 1.4z"/></svg>
        (512)638-2974
      </li>
      <li>
        <svg viewBox="0 0 10 10" aria-hidden="true"><path d="M1 2.5h8v5H1z M1 2.5l4 3 4-3" /></svg>
        marla@valcorne.com
      </li>
      <li>
        <svg viewBox="0 0 10 10" aria-hidden="true"><circle cx="5" cy="5" r="4.5"/></svg>
        valcorne.com
      </li>
    </ul>
  </section>

  <section class="card card--back" aria-label="Card back">
    <div class="back-logo">
      <span class="mark-dot"></span>
      <span class="mark-name">Valcorne<br>Health Care Marketing</span>
    </div>
  </section>
</main>
</body>
</html>
```